Business Card - connecting 2 souls and beggining the journey of self discovery

Logo on the front
with tag line

On the back list of services and contact details

Seminars
workshops
Coaching
podcasts

Darren Whitlow
Health & Wellbeing Life Coach
0491 372 615
darren@brightcoreliving.example
brightcoreliving.example

Industry/Entity Type

Life Coaching

Contact Information for Business Card

I like the use of colour from the logo to be used. I'm not a fan of white.

Requirements
Must have
• My tagline: The journey home starts with you
Nice to have
• Use of colour that is in the mind body soul logo

```html
<!DOCTYPE html>
<html lang="en">
<head>
<meta charset="utf-8">
<title>Brightcore Living – Business Card</title>
<link rel="stylesheet" href="https://fonts.googleapis.com/css2?family=Open+Sans:wght@400;600;700&display=swap">
<style>
  :root {
    --backdrop: #2b2b2d;
    --card-white: #f7f7f6;
    --coral: #f06a6c;
    --orange: #f4a04a;
    --blush: #f7a9b4;
    --leaf: #3fae80;
    --rose: #ee5a6f;
    --ink: #5c5c5c;
    --ink-soft: #7a7a7a;
    --tab-grey: #8d8d8f;
    --white: #ffffff;
  }
  * { margin: 0; padding: 0; box-sizing: border-box; }
  html, body {
    width: 1200px; height: 900px; overflow: hidden;
    background: var(--backdrop);
    font-family: "Open Sans", Arial, sans-serif;
  }
  .canvas { position: relative; width: 1200px; height: 900px; }

  .card {
    position: absolute;
    width: 640px; height: 366px;
    left: 280px;
    border-radius: 4px;
    overflow: hidden;
    box-shadow: 0 10px 30px rgba(0,0,0,0.45);
  }

  /* Front */
  .card-front {
    top: 56px;
    background:
      radial-gradient(ellipse 60% 75% at 50% 38%, var(--orange) 0%, rgba(244,160,74,0) 70%),
      linear-gradient(120deg, var(--blush) 0%, #f3877a 35%, var(--coral) 100%);
    color: var(--white);
    text-align: center;
  }
  .front-mark {
    position: absolute; left: 50%; top: 78px;
    width: 84px; height: 84px; margin-left: -42px;
    border-radius: 50%;
    background: var(--white);
    opacity: 0.9;
  }
  .front-name {
    position: absolute; left: 0; right: 0; top: 184px;
    font-size: 38px; font-weight: 600; letter-spacing: -0.5px;
    color: var(--white);
  }
  .front-services {
    position: absolute; left: 0; right: 0; top: 250px;
    font-size: 14px; font-weight: 400;
    color: var(--white);
    word-spacing: 2px;
  }
  .front-services .dot { margin: 0 6px; }

  /* Back */
  .card-back {
    top: 478px;
    background: var(--card-white);
  }
  .brand-tab {
    position: absolute; right: 150px; top: 0;
    width: 46px; height: 54px;
    background: var(--tab-grey);
  }
  .brand-mark {
    position: absolute; right: 134px; top: 34px;
    width: 78px; height: 78px;
    border-radius: 50%;
    background: var(--orange);
    border: 4px solid var(--white);
  }
  .brand-block {
    position: absolute; right: 34px; top: 128px;
    text-align: left;
  }
  .brand-name {
    font-size: 27px; font-weight: 400; color: var(--ink-soft);
    letter-spacing: -0.4px; line-height: 1.1;
  }
  .brand-tagline {
    font-size: 14px; font-weight: 600; color: var(--ink);
    margin-top: 2px;
  }

  .contact-block {
    position: absolute; left: 40px; bottom: 34px;
  }
  .person-name {
    font-size: 22px; font-weight: 700; color: var(--leaf);
    text-transform: uppercase; letter-spacing: 0.3px; line-height: 1.1;
  }
  .person-role {
    font-size: 18px; font-weight: 700; color: var(--rose);
    text-transform: uppercase; line-height: 1.2; margin-bottom: 10px;
  }
  .contact-list { list-style: none; }
  .contact-item {
    display: flex; align-items: center; gap: 10px;
    font-size: 17px; color: var(--ink); line-height: 1.45;
  }
  .contact-icon { width: 16px; height: 16px; flex: none; }
</style>
</head>
<body>
<main class="canvas">

  <section class="card card-front" aria-label="Card front">
    <span class="front-mark" aria-hidden="true"></span>
    <h1 class="front-name">Brightcore Living</h1>
    <p class="front-services">Seminars<span class="dot">•</span>Workshops<span class="dot">•</span>Coaching<span class="dot">•</span>Podcasts</p>
  </section>

  <section class="card card-back" aria-label="Card back">
    <span class="brand-tab" aria-hidden="true"></span>
    <span class="brand-mark" aria-hidden="true"></span>
    <div class="brand-block">
      <h2 class="brand-name">Brightcore Living</h2>
      <p class="brand-tagline">The journey home starts with you</p>
    </div>

    <div class="contact-block">
      <h3 class="person-name">Darren Whitlow</h3>
      <p class="person-role">Health &amp; Wellbeing Life Coach</p>
      <ul class="contact-list">
        <li class="contact-item">
          <svg class="contact-icon" viewBox="0 0 16 16" aria-hidden="true">
            <circle cx="8" cy="8" r="8" fill="var(--leaf)"/>
            <path d="M5.2 4.2l1.4-.2.8 2-1 .8c.5 1.1 1.3 1.9 2.4 2.4l.8-1 2 .8-.2 1.4c-3.4.4-6.6-2.8-6.2-6.2z" fill="#fff"/>
          </svg>
          0491 372 615
        </li>
        <li class="contact-item">
          <svg class="contact-icon" viewBox="0 0 16 16" aria-hidden="true">
            <circle cx="8" cy="8" r="8" fill="var(--leaf)"/>
            <rect x="4" y="5" width="8" height="6" rx="0.6" fill="#fff"/>
            <path d="M4.3 5.4L8 8.3l3.7-2.9" fill="none" stroke="var(--leaf)" stroke-width="0.9"/>
          </svg>
          darren@brightcoreliving.example
        </li>
        <li class="contact-item">
          <svg class="contact-icon" viewBox="0 0 16 16" aria-hidden="true">
            <circle cx="8" cy="8" r="8" fill="var(--leaf)"/>
            <circle cx="8" cy="8" r="4" fill="none" stroke="#fff" stroke-width="1"/>
            <ellipse cx="8" cy="8" rx="1.7" ry="4" fill="none" stroke="#fff" stroke-width="0.9"/>
            <path d="M4 8h8" stroke="#fff" stroke-width="0.9"/>
          </svg>
          brightcoreliving.example
        </li>
      </ul>
    </div>
  </section>

</main>
</body>
</html>
```